Business Cards for a law firm

Business cards for our law firm. Use our silhoette logo and OAK PARTNERS - check our website (www.oakpartners.example)

Contact Information for Business Card

our silhouette logo, OAK PARTNERS, 800-555-0147, Dorian Pemberton, dorian@oakpartners.example

Requirements
Must have
• our silhouette logo, OAK PARTNERS, 800-555-0147, Dorian Pemberton, dorian@oakpartners.example

```html
<!DOCTYPE html>
<html lang="en">
<head>
<meta charset="utf-8">
<title>Oak Partners — Business Cards</title>
<link href="https://fonts.googleapis.com/css2?family=Montserrat:wght@400;500;700&display=swap" rel="stylesheet">
<style>
  :root {
    --navy: #22336b;
    --white: #ffffff;
    --ink: #1d1f2b;
    --backdrop: #e6e7eb;
    --card-radius: 24px;
  }
  * { box-sizing: border-box; margin: 0; padding: 0; }
  html, body {
    width: 1200px; height: 900px; overflow: hidden;
    background: var(--backdrop);
  }
  .canvas { position: relative; width: 1200px; height: 900px; }
  .card {
    position: absolute; left: 290px; width: 620px; height: 354px;
    border-radius: var(--card-radius);
    overflow: hidden;
    box-shadow: 0 6px 18px rgba(20, 24, 40, 0.18);
  }
  .card--back { top: 70px; background: var(--navy); }
  .card--front { top: 476px; background: var(--white); }

  .brand {
    display: flex; align-items: center; gap: 18px;
    color: var(--white);
    font-family: "Montserrat", sans-serif;
    font-weight: 500;
    letter-spacing: 0.02em;
    white-space: nowrap;
  }
  .brand__mark {
    width: 16px; height: 16px; background: var(--white); flex: none;
  }
  .card--back .brand {
    position: absolute; left: 110px; top: 150px; font-size: 38px;
  }

  .front__band {
    position: absolute; left: 0; top: 0; width: 100%; height: 218px;
    background: var(--navy);
  }
  .card--front .brand {
    position: absolute; left: 60px; top: 92px; font-size: 40px;
  }

  .holder {
    position: absolute; right: 352px; top: 250px; text-align: right;
    color: var(--navy);
  }
  .holder__name {
    font-family: "Montserrat", sans-serif; font-weight: 700;
    font-size: 25px; letter-spacing: 0.01em; white-space: nowrap;
  }
  .holder__role {
    font-family: "Montserrat", sans-serif; font-weight: 400;
    font-size: 15px; color: var(--ink); margin-top: 2px;
  }
  .divider {
    position: absolute; left: 296px; top: 246px; width: 2px; height: 74px;
    background: var(--navy);
  }
  .contact {
    position: absolute; left: 322px; top: 250px;
    list-style: none;
    font-family: "Montserrat", sans-serif; font-weight: 500;
    font-size: 15px; color: var(--ink); line-height: 23px;
  }
  .contact__item { display: flex; align-items: center; gap: 10px; }
  .contact__icon { width: 13px; height: 13px; flex: none; fill: var(--navy); }
</style>
</head>
<body>
<main class="canvas">

  <section class="card card--back" aria-label="Card back">
    <div class="brand"><span class="brand__mark"></span>OAK PARTNERS</div>
  </section>

  <section class="card card--front" aria-label="Card front">
    <div class="front__band"></div>
    <div class="brand"><span class="brand__mark"></span>OAK PARTNERS</div>

    <div class="holder">
      <p class="holder__name">Dorian Pemberton</p>
      <p class="holder__role">Attorney at Law</p>
    </div>
    <span class="divider"></span>

    <ul class="contact">
      <li class="contact__item">
        <svg class="contact__icon" viewBox="0 0 16 16" aria-hidden="true"><path d="M3.6 1.2l2.3 2.6-1.3 2.1c.9 2 2.5 3.6 4.5 4.5l2.1-1.3 2.6 2.3-1.2 2.6C6.6 14.8 1.2 9.4 1 3.4z"/></svg>
        800-555-0147
      </li>
      <li class="contact__item">
        <svg class="contact__icon" viewBox="0 0 16 16" aria-hidden="true"><path d="M1 3h14v1.2L8 8.6 1 4.2z"/><path d="M1 5.6l7 4.4 7-4.4V13H1z"/></svg>
        dorian@oakpartners.example
      </li>
      <li class="contact__item">
        <svg class="contact__icon" viewBox="0 0 16 16" aria-hidden="true"><circle cx="8" cy="8" r="7"/><path d="M1 8h14M8 1c2.5 2.2 2.5 11.8 0 14M8 1c-2.5 2.2-2.5 11.8 0 14" stroke="#fff" stroke-width="1" fill="none"/></svg>
        www.oakpartners.example
      </li>
    </ul>
  </section>

</main>
</body>
</html>
```